BRIGHT RIVER POWER.

I'd like my business logo.
contact name: Dennis Halvorsen
phone:0438759164
email: info@brightriverpower.net.au
website: www.brightriverpower.net.au

services:
solar
battery storage
LED lighting
energy saving solutions
general electrical
I'd like the design to look professional

Target Market(s)

Everyone

Industry/Entity Type

Business

Contact Information for Business Card

as described above

Requirements
Must have
• Id like the colours and the design to work well with my logo.

```html
<!DOCTYPE html>
<html lang="en">
<head>
<meta charset="utf-8">
<title>Bright River Power – Business Card</title>
<link href="https://fonts.googleapis.com/css2?family=Arimo:wght@400;700&display=swap" rel="stylesheet">
<style>
  :root {
    --page-bg: #e9ebe8;
    --green-light: #7cc242;
    --green-dark: #2f9a3a;
    --brand-green: #3a9e45;
    --sun-orange: #f0a830;
    --ink: #1f1f1f;
    --card-white: #ffffff;
    --rule-green: #2f9a54;
  }
  * { box-sizing: border-box; margin: 0; padding: 0; }
  html, body {
    width: 1200px; height: 997px; overflow: hidden;
    background: var(--page-bg);
    font-family: "Arimo", Arial, sans-serif;
  }
  .sheet { position: relative; width: 1200px; height: 997px; }
  .card {
    position: absolute; left: 250px; width: 700px; height: 400px;
    border-radius: 26px; overflow: hidden;
    box-shadow: 0 10px 30px rgba(0,0,0,.18);
  }
  /* Front */
  .card-front {
    top: 68px;
    background: linear-gradient(160deg, var(--green-dark) 0%, var(--green-light) 100%);
  }
  .service {
    position: absolute; color: #fff; font-size: 15px;
    letter-spacing: 1.5px; text-transform: uppercase; font-weight: 400;
    white-space: nowrap;
  }
  .service-battery { left: 228px; top: 96px; }
  .service-solar { left: 548px; top: 96px; }
  .service-led { left: 60px; top: 282px; }
  .service-saving { left: 340px; top: 292px; }
  .logo-panel {
    position: absolute; left: 170px; top: 128px; width: 360px; height: 140px;
    background: var(--card-white); border-radius: 22px;
    box-shadow: 0 0 22px rgba(255,255,255,.7);
    display: flex; align-items: center; justify-content: center;
    padding: 0 24px;
  }
  .brand { display: flex; align-items: center; gap: 10px; }
  .brand-dot {
    width: 28px; height: 28px; border-radius: 50%; background: var(--sun-orange);
    flex: none;
  }
  .brand-name {
    color: var(--brand-green); font-weight: 700; font-size: 21px;
    letter-spacing: .5px; white-space: nowrap;
  }
  /* Back */
  .card-back { top: 528px; background: var(--card-white); }
  .card-back .brand { position: absolute; right: 42px; top: 38px; }
  .rule {
    position: absolute; left: 216px; top: 188px; width: 444px; height: 2px;
    background: var(--rule-green);
  }
  .decor-mark {
    position: absolute; right: 56px; top: 206px; width: 120px; height: 120px;
    border-radius: 50%;
    background: radial-gradient(circle at 60% 45%, rgba(124,194,66,.45), rgba(240,168,48,.25));
  }
  .person { position: absolute; left: 40px; top: 170px; }
  .person-name { color: var(--brand-green); font-weight: 700; font-size: 18px; white-space: nowrap; }
  .person-role { color: var(--ink); font-size: 18px; margin-top: 2px; }
  .contacts { position: absolute; left: 40px; top: 256px; list-style: none; }
  .contacts li {
    display: flex; align-items: center; gap: 14px;
    color: var(--ink); font-size: 18px; margin-bottom: 14px;
  }
  .contacts svg { width: 16px; height: 16px; flex: none; }
</style>
</head>
<body>
<main class="sheet">
  <section class="card card-front" aria-label="Card front">
    <span class="service service-battery">Battery Storage</span>
    <span class="service service-solar">Solar</span>
    <div class="logo-panel">
      <div class="brand">
        <span class="brand-dot"></span>
        <span class="brand-name">BRIGHT RIVER POWER</span>
      </div>
    </div>
    <span class="service service-led">LED Lighting</span>
    <span class="service service-saving">Energy Saving Solutions</span>
  </section>

  <section class="card card-back" aria-label="Card back">
    <div class="brand">
      <span class="brand-dot"></span>
      <span class="brand-name">BRIGHT RIVER POWER</span>
    </div>
    <div class="rule"></div>
    <div class="decor-mark" role="img" aria-label="Faint brand emblem area"></div>
    <div class="person">
      <p class="person-name">Dennis Halvorsen</p>
      <p class="person-role">Director</p>
    </div>
    <ul class="contacts">
      <li>
        <svg viewBox="0 0 16 16" aria-hidden="true"><path fill="#2f9a3a" d="M3 1l3 3-1.5 2a9 9 0 0 0 5.5 5.5L12 10l3 3-2 2C6 15 1 10 1 3z"/></svg>
        <span>0438759164</span>
      </li>
      <li>
        <svg viewBox="0 0 16 16" aria-hidden="true"><rect x="1" y="3" width="14" height="10" rx="1" fill="#2f9a3a"/><path d="M1.5 3.5L8 9l6.5-5.5" stroke="#fff" stroke-width="1.2" fill="none"/></svg>
        <span>info@brightriverpower.net.au</span>
      </li>
      <li>
        <svg viewBox="0 0 16 16" aria-hidden="true"><circle cx="8" cy="8" r="7" fill="#2f9a3a"/><path d="M1 8h14M8 1c-3 3-3 11 0 14M8 1c3 3 3 11 0 14" stroke="#fff" stroke-width="1" fill="none"/></svg>
        <span>www.brightriverpower.net.au</span>
      </li>
    </ul>
  </section>
</main>
</body>
</html>
```